Freelance business trainer needs a new business card

My business is called Brontlearn. I provide training in the workplace on management, coaching and mentoring, and customer service topics for a variety of businesses, colleges and private training providers, and teach on management programs. I need a professional but eye catching business card. Business colours grey and orange. My name Marion Tadwick; Tel 07382 415067; email mtadwick@brontlearn.co.uk; website www.brontlearn.co.uk.
Happy to have some sort of logo on front and details on back or all on one side
Target Market(s)
SME businesses and colleges - workshops i run are for adults in the workplace
Industry/Entity Type
Training
Look and feel

```html
<!DOCTYPE html>
<html lang="en">
<head>
<meta charset="utf-8">
<title>Brontlearn – Business Card</title>
<link rel="stylesheet" href="https://fonts.googleapis.com/css2?family=Open+Sans:wght@400;600;700&display=swap">
<style>
  :root {
    --charcoal: #404040;
    --orange: #f39022;
    --white: #ffffff;
    --backdrop: #e8e8e8;
    --icon-dark: #3a3a3a;
  }
  * { margin: 0; padding: 0; box-sizing: border-box; }
  html, body {
    width: 1200px; height: 1183px; overflow: hidden;
    background: var(--backdrop);
    font-family: "Open Sans", Arial, sans-serif;
  }
  .sheet { position: relative; width: 1200px; height: 1183px; }
  .card {
    position: absolute; left: 160px; width: 880px; height: 503px;
    border-radius: 34px; overflow: hidden;
    background: var(--charcoal);
    box-shadow: 0 6px 18px rgba(0,0,0,0.18);
  }
  .card--front { top: 60px; }
  .card--back { top: 620px; }
  .card__shapes { position: absolute; inset: 0; }

  .wordmark {
    position: absolute; display: flex; align-items: center; gap: 14px;
    color: var(--orange); font-weight: 600; letter-spacing: 1px; line-height: 1;
    white-space: nowrap;
  }
  .wordmark__square { width: 0.62em; height: 0.62em; background: var(--orange); }
  .card--front .wordmark { left: 0; right: 0; top: 190px; justify-content: center; font-size: 78px; }
  .card--back .wordmark { left: 50px; top: 212px; font-size: 42px; gap: 12px; }

  .front__web {
    position: absolute; left: 0; right: 0; top: 346px;
    display: flex; align-items: center; justify-content: center; gap: 18px;
    color: var(--white); font-size: 24px; letter-spacing: 1px;
  }
  .front__rule { width: 170px; height: 1px; background: rgba(255,255,255,0.6); }

  .holder { position: absolute; left: 500px; top: 58px; color: var(--white); }
  .holder__name { font-size: 24px; font-weight: 700; }
  .holder__role { font-size: 20px; font-weight: 400; margin-left: 110px; margin-top: 2px; }

  .contact {
    position: absolute; right: 44px; top: 282px; list-style: none;
    color: var(--white); font-size: 21px; text-align: right; white-space: nowrap;
  }
  .contact__item { display: flex; align-items: center; justify-content: flex-end; gap: 12px; margin-bottom: 14px; }
  .contact__icon { width: 22px; height: 22px; flex: none; }
</style>
</head>
<body>
<main class="sheet">

  <section class="card card--front" aria-label="Card front">
    <div class="wordmark"><span class="wordmark__square"></span>Brontlearn</div>
    <div class="front__web"><span class="front__rule"></span>www.brontlearn.co.uk<span class="front__rule"></span></div>
  </section>

  <section class="card card--back" aria-label="Card back">
    <svg class="card__shapes" viewBox="0 0 880 503" width="880" height="503" aria-hidden="true">
      <polygon points="300,0 352,0 420,230 880,128 880,503 478,503" fill="var(--white)"/>
      <polygon points="446,262 880,176 880,503 542,503" fill="var(--orange)"/>
    </svg>

    <div class="wordmark"><span class="wordmark__square"></span>Brontlearn</div>

    <div class="holder">
      <p class="holder__name">Marion Tadwick</p>
      <p class="holder__role">Owner</p>
    </div>

    <ul class="contact">
      <li class="contact__item">07382 415067
        <svg class="contact__icon" viewBox="0 0 24 24" aria-hidden="true"><circle cx="12" cy="12" r="12" fill="var(--icon-dark)"/><path d="M8 6.5c.6-.5 1.4-.4 1.8.2l1 1.6c.3.5.2 1.1-.2 1.5l-.8.7c.6 1.3 1.6 2.4 2.9 3l.7-.8c.4-.4 1-.5 1.5-.2l1.6 1c.6.4.7 1.2.2 1.8l-.8.9c-.6.6-1.5.8-2.3.5-3-1.1-5.3-3.5-6.4-6.4-.3-.8-.1-1.700.5-2.3z" fill="var(--white)"/></svg>
      </li>
      <li class="contact__item">mtadwick@brontlearn.co.uk
        <svg class="contact__icon" viewBox="0 0 24 24" aria-hidden="true"><circle cx="12" cy="12" r="12" fill="var(--icon-dark)"/><rect x="6" y="8" width="12" height="8.5" rx="1" fill="var(--white)"/><path d="M6.5 8.6 12 12.8l5.5-4.2" fill="none" stroke="var(--icon-dark)" stroke-width="1.2"/></svg>
      </li>
      <li class="contact__item">www.brontlearn.co.uk
        <svg class="contact__icon" viewBox="0 0 24 24" aria-hidden="true"><circle cx="12" cy="12" r="12" fill="var(--icon-dark)"/><g fill="none" stroke="var(--white)" stroke-width="1.3"><circle cx="12" cy="12" r="6.5"/><ellipse cx="12" cy="12" rx="2.8" ry="6.5"/><path d="M5.5 12h13M6.5 8.8h11M6.5 15.2h11"/></g></svg>
      </li>
    </ul>
  </section>

</main>
</body>
</html>
```